Business IT Services Billboard to attract local small businesses

We are Brivoqua, a premier Managed Service Provider (MSP) specializing in comprehensive IT services and VOIP phone solutions exclusively for businesses. Our goal is to create a dynamic and visually engaging billboard advertisement that not only highlights our cutting-edge IT solutions but also emphasizes our state-of-the-art VOIP phone services. This billboard should communicate our commitment to providing innovative, reliable, and holistic technology solutions.
See the attached supporting documentation.
Target Market(s)
small business
Industry/Entity Type
Information Technology
Colors
Designer to choose colors to be used in the design.
Look and feel
Each slider illustrates characteristics of the customer's brand and the style your logo design should communicate.

```html
<!DOCTYPE html>
<html lang="en">
<head>
<meta charset="utf-8">
<title>Brivoqua Billboard</title>
<link rel="stylesheet" href="https://fonts.googleapis.com/css2?family=Montserrat:wght@600;700;800&family=Poppins:wght@600&family=Saira+Semi+Condensed:wght@600&display=swap">
<style>
  :root {
    --backdrop: #c9c9c9;
    --white: #ffffff;
    --brand-blue: #1565b0;
    --band-blue: #1a5f9f;
    --band-blue-light: #5aa4dd;
    --orange: #e0570f;
    --navy: #0f1f36;
    --label-grey: #a9abae;
    --photo-light: #e6eef6;
    --photo-mid: #b9cfe4;
    --photo-dark: #3c4a5e;
  }
  * { margin: 0; padding: 0; box-sizing: border-box; }
  html, body { width: 1185px; height: 1200px; overflow: hidden; }
  body {
    background: radial-gradient(ellipse at 50% 30%, #e3e3e3 0%, var(--backdrop) 70%);
    position: relative;
  }
  .billboard {
    position: absolute;
    left: 40px; top: 439px;
    width: 1105px; height: 322px;
    overflow: hidden;
    background: var(--white);
    box-shadow: 0 18px 26px rgba(0,0,0,0.28);
  }
  .header { position: absolute; left: 0; top: 0; width: 100%; height: 82px; background: var(--white); }
  .brand-name {
    position: absolute; left: 45px; top: 18px;
    font-family: "Montserrat", sans-serif; font-weight: 800;
    font-size: 44px; letter-spacing: 2px; line-height: 1;
    color: var(--brand-blue);
  }
  .headline-band {
    position: absolute; left: 0; top: 82px; width: 100%; height: 133px;
    background: linear-gradient(90deg, var(--band-blue) 0%, var(--band-blue) 45%, var(--band-blue-light) 62%, rgba(90,164,221,0) 78%);
  }
  .seamless-tag {
    position: absolute; left: 44px; top: 21px;
    width: 22px; height: 84px;
    background: var(--label-grey); border-radius: 3px;
    display: flex; align-items: center; justify-content: center;
  }
  .seamless-tag span {
    transform: rotate(-90deg);
    font-family: "Montserrat", sans-serif; font-weight: 700;
    font-size: 10px; letter-spacing: 1px; color: var(--white); white-space: nowrap;
  }
  .headline {
    position: absolute; left: 73px; top: 14px;
    font-family: "Saira Semi Condensed", sans-serif; font-weight: 600;
    font-size: 48px; line-height: 49px; color: var(--white);
  }
  .tagline-band {
    position: absolute; left: 0; top: 215px; width: 100%; height: 42px;
    background: linear-gradient(90deg, var(--orange) 0%, var(--orange) 55%, rgba(224,87,15,0.6) 68%, rgba(224,87,15,0) 80%);
  }
  .tagline {
    position: absolute; left: 45px; top: 11px;
    font-family: "Poppins", sans-serif; font-weight: 600;
    font-size: 16px; line-height: 20px; color: var(--white);
  }
  .photo {
    position: absolute; left: 640px; top: 0; width: 465px; height: 257px;
    background:
      radial-gradient(ellipse at 75% 55%, var(--photo-dark) 0%, rgba(60,74,94,0.7) 22%, rgba(60,74,94,0) 48%),
      linear-gradient(90deg, rgba(230,238,246,0) 0%, var(--photo-light) 22%, var(--photo-mid) 60%, #9fb6cc 100%);
  }
  .contact-bar {
    position: absolute; left: 0; top: 257px; width: 100%; height: 65px;
    background: var(--navy);
    display: flex; align-items: center;
    padding-left: 45px;
    color: var(--white);
    font-family: "Montserrat", sans-serif;
  }
  .call-label { font-weight: 600; font-size: 18px; margin-right: 22px; }
  .phone-icon { width: 28px; height: 28px; margin-right: 8px; }
  .phone-number { font-weight: 700; font-size: 38px; letter-spacing: 0.5px; }
  .divider { width: 1px; height: 30px; background: rgba(255,255,255,0.7); margin: 0 18px; }
  .cta { font-weight: 700; font-size: 14px; line-height: 16px; margin-right: 22px; }
  .website { font-weight: 700; font-size: 21px; }
  .website .accent { color: var(--orange); }
</style>
</head>
<body>
  <div class="billboard">
    <div class="header">
      <div class="brand-name">BRIVOQUA</div>
    </div>
    <div class="photo" role="img" aria-label="Office desk telephone with a headset resting beside it, soft blue background with floating connection icons"></div>
    <div class="headline-band">
      <div class="seamless-tag"><span>SEAMLESS</span></div>
      <h1 class="headline">TECHNOLOGY SOLUTIONS<br>FOR MODERN BUSINESSES</h1>
    </div>
    <div class="tagline-band">
      <p class="tagline">Innovative IT and VOIP Solutions Tailored for Your Business Success.</p>
    </div>
    <div class="contact-bar">
      <span class="call-label">CALL US TODAY</span>
      <svg class="phone-icon" viewBox="0 0 24 24" aria-hidden="true">
        <path fill="#e0570f" d="M6.6 10.8a15.1 15.1 0 0 0 6.6 6.6l2.2-2.2a1 1 0 0 1 1-.25 11.4 11.4 0 0 0 3.6.57 1 1 0 0 1 1 1V20a1 1 0 0 1-1 1A17 17 0 0 1 3 4a1 1 0 0 1 1-1h3.5a1 1 0 0 1 1 1c0 1.25.2 2.45.57 3.57a1 1 0 0 1-.25 1z"/>
        <path fill="none" stroke="#e0570f" stroke-width="1.6" stroke-linecap="round" d="M14 6.5a4 4 0 0 1 3.5 3.5M14 3a7.5 7.5 0 0 1 7 7"/>
      </svg>
      <span class="phone-number">(555) 014-2736</span>
      <span class="divider"></span>
      <span class="cta">TRANSFORM YOUR<br>TECH TODAY AT</span>
      <span class="website">www.<span class="accent">brivoqua</span>.com</span>
    </div>
  </div>
</body>
</html>
```